Corvena Hotel, city center modern minimal hotel operating all year round, on Rhodes island Greece

city, modern ,all year operating hotel

Target Market(s)

tourists, business agents

Industry/Entity Type

tourism

Number of Pages Required

2 page

Requirements
Must have
• room type photos and descriptions, amenities individual listing (graphic), comments sections, map driving location details
Nice to have
• gallery section, modern and minimal design, amenities section, individual room type descriptions, photos and facilities

```html
<!DOCTYPE html>
<html lang="en">
<head>
<meta charset="utf-8">
<title>Corvena Hotel – Room List</title>
<link rel="stylesheet" href="https://fonts.googleapis.com/css2?family=Rubik:wght@400;500&family=Nunito+Sans:wght@400;600&display=swap">
<style>
:root{
  --gold:#bd9440;
  --ink:#151a22;
  --text:#1c1f26;
  --muted:#6b6f78;
  --line:#e4e4e4;
  --footer:#131a24;
  --white:#fff;
}
*{box-sizing:border-box;margin:0;padding:0}
html,body{width:721px;height:1200px;overflow:hidden;background:#fff}
.page{position:relative;width:1366px;height:2273px;transform:scale(.5278);transform-origin:0 0;font-family:"Nunito Sans",sans-serif;color:var(--text)}
.abs{position:absolute}
h1,h2,h3,h4,.nav a,.btn{font-family:"Rubik",sans-serif;font-weight:400}

/* hero */
.hero{left:0;top:0;width:1366px;height:451px;background:linear-gradient(120deg,#2c2f37 0%,#3b3d45 40%,#2a2c33 70%,#34363e 100%)}
.brand{left:55px;top:32px;display:flex;align-items:center;gap:14px;color:var(--white);font-family:"Rubik",sans-serif;font-size:28px;white-space:nowrap}
.brand .mark{width:50px;height:50px;background:var(--gold);display:block}
.nav{left:377px;top:48px;display:flex}
.nav a{color:var(--white);font-size:18px;font-weight:500;text-decoration:none;margin-right:56px}
.btn{display:flex;align-items:center;justify-content:center;gap:14px;background:var(--gold);color:var(--white);font-weight:500;font-size:16px;text-transform:uppercase}
.book{left:1085px;top:30px;width:202px;height:60px}
.page-title{left:0;width:1366px;top:236px;text-align:center;color:var(--white);font-size:46px;line-height:56px}
.crumbs{left:0;width:1366px;top:305px;text-align:center;font-family:"Rubik",sans-serif;font-size:14px;font-weight:500;color:var(--white)}
.crumbs span{color:var(--gold)}

/* sidebar */
.widget{left:125px;width:261px;border:1px solid var(--line);padding:32px 30px}
.widget h3{font-size:20px;color:var(--text);padding-bottom:12px;position:relative}
.widget h3::after{content:"";position:absolute;left:0;bottom:0;width:60px;height:1px;background:var(--gold)}
.cats{list-style:none;margin-top:20px}
.cats li{display:flex;justify-content:space-between;font-size:15px;height:51px;align-items:center;border-bottom:1px solid var(--line)}
.field{height:60px;border:1px solid var(--line);display:flex;align-items:center;justify-content:space-between;padding:0 15px;font-size:15px;margin-top:10px}
.check{width:170px;height:60px;margin-top:30px}

/* rooms */
.room{left:410px;width:831px;height:195px;border:1px solid var(--line)}
.room .photo{position:absolute;left:0;top:0;width:231px;height:193px}
.room h2{position:absolute;left:282px;top:24px;font-size:24px}
.room p{position:absolute;left:282px;top:56px;width:340px;font-size:14.5px;line-height:26px;color:var(--muted)}
.room .meta{position:absolute;left:282px;top:152px;display:flex;gap:28px;font-size:14.5px;color:#444}
.meta span{display:flex;align-items:center;gap:8px}
.room .sep{position:absolute;left:641px;top:20px;width:1px;height:155px;background:var(--line)}
.price{position:absolute;left:642px;width:188px;top:62px;text-align:center;font-size:14.5px}
.price .rate{color:var(--gold);font-weight:600}
.price .stars{margin-top:4px;display:flex;justify-content:center;gap:8px;align-items:center}
.price .more{margin-top:8px;display:flex;justify-content:center;gap:8px;align-items:center;font-family:"Rubik",sans-serif;font-size:14px}

/* footer */
.footer{left:0;top:1784px;width:1366px;height:489px;background:var(--footer);color:#dfe2e7}
.f-brand{left:125px;top:75px;display:flex;align-items:center;gap:12px;font-family:"Rubik",sans-serif;font-size:26px;color:var(--white);white-space:nowrap}
.f-brand .mark{width:44px;height:44px;background:var(--gold);display:block}
.f-about{left:125px;top:150px;width:260px;font-size:15px;line-height:26px}
.socials{left:125px;top:231px;display:flex;gap:13px}
.socials i{width:40px;height:40px;border:1px solid #3a424e;border-radius:50%;display:block}
.footer h4{font-size:20px;font-weight:500;color:var(--white)}
.info{left:410px;top:160px;font-size:15px;line-height:26px}
.info li{list-style:none;display:flex;gap:16px;margin-bottom:16px}
.links li{list-style:none;font-size:15px;margin-bottom:10px}
.subscribe{left:885px;top:155px;width:356px;height:70px;border:1px solid #2d3540;display:flex}
.subscribe .input{flex:1;display:flex;align-items:center;padding-left:20px;font-size:15px;color:#8a919c}
.subscribe .go{width:70px;background:var(--gold);display:flex;align-items:center;justify-content:center}
.f-rule{left:0;top:381px;width:1366px;height:1px;background:#252d38}
.copy{left:125px;top:427px;font-size:15px;color:var(--white)}
.copy span{color:var(--gold)}
.legal{right:125px;top:427px;font-size:15px;display:flex;gap:16px;color:var(--white)}
.legal b{font-weight:400;color:#555d69}
.totop{left:1296px;top:419px;width:50px;height:50px;border:1px solid var(--gold);border-radius:50%;display:flex;align-items:center;justify-content:center}
</style>
</head>
<body>
<div class="page">

  <header class="hero abs" role="img" aria-label="Dimly lit hotel bedroom with a made bed and bench"></header>
  <div class="brand abs"><i class="mark"></i>Corvena Hotel</div>
  <nav class="nav abs"><a>Home +</a><a>Pages +</a><a>Room +</a><a>Blog +</a><a>Contact</a></nav>
  <div class="btn book abs">Book Now
    <svg width="18" height="12" viewBox="0 0 18 12" fill="none" stroke="#fff" stroke-width="1.8"><path d="M0 6h16M11 1l5 5-5 5"/></svg></div>
  <h1 class="page-title abs">Room List</h1>
  <div class="crumbs abs">Home &nbsp;- &nbsp;<span>Room List</span></div>

  <aside class="widget abs" style="top:571px;height:377px">
    <h3>Category</h3>
    <ul class="cats">
      <li><span>» Luxury Room</span><span>(08)</span></li>
      <li><span>» Small Suite</span><span>(06)</span></li>
      <li><span>» Single</span><span>(05)</span></li>
      <li><span>» Family</span><span>(09)</span></li>
      <li><span>» Double Room</span><span>(03)</span></li>
    </ul>
  </aside>
  <aside class="widget abs" style="top:978px;height:422px">
    <h3>Booking Now</h3>
    <div style="height:20px"></div>
    <div class="field">Check In<svg width="14" height="8" viewBox="0 0 14 8" fill="none" stroke="#555" stroke-width="1.3"><path d="M1 1l6 6 6-6"/></svg></div>
    <div class="field">Check Out<svg width="14" height="8" viewBox="0 0 14 8" fill="none" stroke="#555" stroke-width="1.3"><path d="M1 1l6 6 6-6"/></svg></div>
    <div class="field">Room<svg width="14" height="8" viewBox="0 0 14 8" fill="none" stroke="#555" stroke-width="1.3"><path d="M1 1l6 6 6-6"/></svg></div>
    <div class="btn check">Check
      <svg width="18" height="12" viewBox="0 0 18 12" fill="none" stroke="#fff" stroke-width="1.8"><path d="M0 6h16M11 1l5 5-5 5"/></svg></div>
  </aside>

  <article class="room abs" style="top:571px">
    <div class="photo" role="img" aria-label="Superior room with a bed and cushions" style="background:linear-gradient(135deg,#e9ded0,#b79c80)"></div>
    <h2>Superior Room</h2>
    <p>Savvy travelers are looking for more than just the next destination on the map. They are looking for a memorable experience.</p>
    <div class="meta"><span><svg width="16" height="12" viewBox="0 0 16 12" fill="none" stroke="#b99a55" stroke-width="1.2"><path d="M1 1v10M1 7h14v4M4 7V4h10v3"/></svg>(3) bed's</span><span><svg width="20" height="12" viewBox="0 0 20 12" fill="none" stroke="#b99a55" stroke-width="1.2"><circle cx="6" cy="4" r="2.5"/><circle cx="14" cy="4" r="2.5"/><path d="M1 11c0-3 10-3 10 0M9 11c0-3 10-3 10 0"/></svg>(7) Guest's</span></div>
    <div class="sep"></div>
    <div class="price"><div class="rate">$249/Night</div><div class="stars"><svg width="14" height="13" viewBox="0 0 14 13"><path fill="#bd9440" d="M7 0l2.1 4.3 4.9.7-3.5 3.4.8 4.6L7 10.8 2.7 13l.8-4.6L0 5l4.9-.7z"/></svg>2.9 &nbsp;2k</div><div class="more"><svg width="18" height="18" viewBox="0 0 18 18" fill="none" stroke="#bd9440"><circle cx="9" cy="9" r="8"/><path d="M7.5 5.5L11 9l-3.5 3.5"/></svg>READ MORE</div></div>
  </article>

  <article class="room abs" style="top:796px">
    <div class="photo" role="img" aria-label="Junior suite with a sofa and small table" style="background:linear-gradient(135deg,#d9d4cc,#a4876a)"></div>
    <h2>Junior Suite</h2>
    <p>Savvy travelers are looking for more than just the next destination on the map. They are looking for a memorable experience.</p>
    <div class="meta"><span><svg width="16" height="12" viewBox="0 0 16 12" fill="none" stroke="#b99a55" stroke-width="1.2"><path d="M1 1v10M1 7h14v4M4 7V4h10v3"/></svg>(4) bed's</span><span><svg width="20" height="12" viewBox="0 0 20 12" fill="none" stroke="#b99a55" stroke-width="1.2"><circle cx="6" cy="4" r="2.5"/><circle cx="14" cy="4" r="2.5"/><path d="M1 11c0-3 10-3 10 0M9 11c0-3 10-3 10 0"/></svg>(2) Guest's</span></div>
    <div class="sep"></div>
    <div class="price"><div class="rate">$205/Night</div><div class="stars"><svg width="14" height="13" viewBox="0 0 14 13"><path fill="#bd9440" d="M7 0l2.1 4.3 4.9.7-3.5 3.4.8 4.6L7 10.8 2.7 13l.8-4.6L0 5l4.9-.7z"/></svg>3.9 &nbsp;2k</div><div class="more"><svg width="18" height="18" viewBox="0 0 18 18" fill="none" stroke="#bd9440"><circle cx="9" cy="9" r="8"/><path d="M7.5 5.5L11 9l-3.5 3.5"/></svg>READ MORE</div></div>
  </article>

  <article class="room abs" style="top:1020px">
    <div class="photo" role="img" aria-label="Double room with a bed and bedside lamps" style="background:linear-gradient(135deg,#cdb79a,#8f6f50)"></div>
    <h2>Double Room</h2>
    <p>Savvy travelers are looking for more than just the next destination on the map. They are looking for a memorable experience.</p>
    <div class="meta"><span><svg width="16" height="12" viewBox="0 0 16 12" fill="none" stroke="#b99a55" stroke-width="1.2"><path d="M1 1v10M1 7h14v4M4 7V4h10v3"/></svg>(3) bed's</span><span><svg width="20" height="12" viewBox="0 0 20 12" fill="none" stroke="#b99a55" stroke-width="1.2"><circle cx="6" cy="4" r="2.5"/><circle cx="14" cy="4" r="2.5"/><path d="M1 11c0-3 10-3 10 0M9 11c0-3 10-3 10 0"/></svg>(4) Guest's</span></div>
    <div class="sep"></div>
    <div class="price"><div class="rate">$219/Night</div><div class="stars"><svg width="14" height="13" viewBox="0 0 14 13"><path fill="#bd9440" d="M7 0l2.1 4.3 4.9.7-3.5 3.4.8 4.6L7 10.8 2.7 13l.8-4.6L0 5l4.9-.7z"/></svg>4.9 &nbsp;2k</div><div class="more"><svg width="18" height="18" viewBox="0 0 18 18" fill="none" stroke="#bd9440"><circle cx="9" cy="9" r="8"/><path d="M7.5 5.5L11 9l-3.5 3.5"/></svg>READ MORE</div></div>
  </article>

  <article class="room abs" style="top:1245px">
    <div class="photo" role="img" aria-label="Small suite with a bed by a bright window" style="background:linear-gradient(135deg,#efe8dc,#b9a488)"></div>
    <h2>Small Suite</h2>
    <p>Savvy travelers are looking for more than just the next destination on the map. They are looking for a memorable experience.</p>
    <div class="meta"><span><svg width="16" height="12" viewBox="0 0 16 12" fill="none" stroke="#b99a55" stroke-width="1.2"><path d="M1 1v10M1 7h14v4M4 7V4h10v3"/></svg>(2) bed's</span><span><svg width="20" height="12" viewBox="0 0 20 12" fill="none" stroke="#b99a55" stroke-width="1.2"><circle cx="6" cy="4" r="2.5"/><circle cx="14" cy="4" r="2.5"/><path d="M1 11c0-3 10-3 10 0M9 11c0-3 10-3 10 0"/></svg>(3) Guest's</span></div>
    <div class="sep"></div>
    <div class="price"><div class="rate">$188/Night</div><div class="stars"><svg width="14" height="13" viewBox="0 0 14 13"><path fill="#bd9440" d="M7 0l2.1 4.3 4.9.7-3.5 3.4.8 4.6L7 10.8 2.7 13l.8-4.6L0 5l4.9-.7z"/></svg>4.4 &nbsp;2k</div><div class="more"><svg width="18" height="18" viewBox="0 0 18 18" fill="none" stroke="#bd9440"><circle cx="9" cy="9" r="8"/><path d="M7.5 5.5L11 9l-3.5 3.5"/></svg>READ MORE</div></div>
  </article>

  <article class="room abs" style="top:1470px">
    <div class="photo" role="img" aria-label="Luxury room with a pale blue bed and artwork" style="background:linear-gradient(135deg,#e6ddd2,#a9b9c7)"></div>
    <h2>Luxury Room</h2>
    <p>Savvy travelers are looking for more than just the next destination on the map. They are looking for a memorable experience.</p>
    <div class="meta"><span><svg width="16" height="12" viewBox="0 0 16 12" fill="none" stroke="#b99a55" stroke-width="1.2"><path d="M1 1v10M1 7h14v4M4 7V4h10v3"/></svg>(3) bed's</span><span><svg width="20" height="12" viewBox="0 0 20 12" fill="none" stroke="#b99a55" stroke-width="1.2"><circle cx="6" cy="4" r="2.5"/><circle cx="14" cy="4" r="2.5"/><path d="M1 11c0-3 10-3 10 0M9 11c0-3 10-3 10 0"/></svg>(6) Guest's</span></div>
    <div class="sep"></div>
    <div class="price"><div class="rate">$229/Night</div><div class="stars"><svg width="14" height="13" viewBox="0 0 14 13"><path fill="#bd9440" d="M7 0l2.1 4.3 4.9.7-3.5 3.4.8 4.6L7 10.8 2.7 13l.8-4.6L0 5l4.9-.7z"/></svg>3.7 &nbsp;2k</div><div class="more"><svg width="18" height="18" viewBox="0 0 18 18" fill="none" stroke="#bd9440"><circle cx="9" cy="9" r="8"/><path d="M7.5 5.5L11 9l-3.5 3.5"/></svg>READ MORE</div></div>
  </article>

  <footer class="footer abs">
    <div class="f-brand abs"><i class="mark"></i>Corvena Hotel</div>
    <p class="f-about abs">Phasellus nisi sapien, rutrum placerat sapien eu, rhoncus tempus</p>
    <div class="socials abs"><i></i><i></i><i></i><i></i></div>

    <h4 class="abs" style="left:410px;top:94px">Information</h4>
    <ul class="info abs">
      <li><svg width="30" height="28" viewBox="0 0 30 28" fill="none" stroke="#bd9440" stroke-width="1.4"><path d="M1 8l8-3 12 4 8-3v19l-8 3-12-4-8 3z"/><circle cx="15" cy="10" r="3"/></svg><span>14 Ermou Street Rhodes Town,<br>Greece</span></li>
      <li><svg width="30" height="24" viewBox="0 0 30 24" fill="none" stroke="#bd9440" stroke-width="1.4"><rect x="2" y="6" width="26" height="17"/><path d="M2 6l13 9 13-9M8 6V1h14v5"/></svg><span>stay@corvenahotel.gr</span></li>
      <li><svg width="30" height="26" viewBox="0 0 30 26" fill="none" stroke="#bd9440" stroke-width="1.4"><path d="M4 2l5-1 3 6-3 3c2 4 5 7 9 9l3-3 6 3-1 5C13 25 2 14 4 2z"/></svg><span>+30 (224) 100 2417</span></li>
    </ul>

    <h4 class="abs" style="left:695px;top:94px">Pages Links</h4>
    <ul class="links abs" style="left:697px;top:151px">
      <li>Room Cleaning</li><li>Car Parking</li><li>Swimming pool</li><li>Fitness Gym</li>
    </ul>

    <h4 class="abs" style="left:885px;top:94px">Subscribe</h4>
    <div class="subscribe abs"><div class="input">Email Address</div><div class="go"><svg width="18" height="14" viewBox="0 0 18 14" fill="none" stroke="#fff" stroke-width="1.8"><path d="M0 7h16M11 2l5 5-5 5"/></svg></div></div>

    <div class="f-rule abs"></div>
    <p class="copy abs">Copyright 2022 <span>Corvena Hotel</span>, All rights reserved.</p>
    <div class="legal abs"><span>FAQ</span><b>|</b><span>Terms of Use</span><b>|</b><span>Privacy Policy</span></div>
    <div class="totop abs"><svg width="14" height="18" viewBox="0 0 14 18" fill="none" stroke="#fff" stroke-width="1.6"><path d="M7 18V2M1 8l6-6 6 6"/></svg></div>
  </footer>
</div>
</body>
</html>
```